Lumen Fitness Personal Training Business

I need a business card design with a logo for my personal training company. I'd like the colors to be a vibrant green and black. I'd like the logo to incorporate an anvil (or something similar). I train hardcore competitive athletes as well as soccer moms trying to get and/or stay in shape. I need a logo that will not pigeon hole me in one category or the other, but at the same time not be too intimidating to soccer moms, but will not be off putting to the more hardcore trainees. The design should be attention grabbing and aesthetic.
Target Market(s)
Hardcore athletes as well as average people just trying to get/stay in shape.
Industry/Entity Type
Training

```html
<!DOCTYPE html>
<html lang="en">
<head>
<meta charset="utf-8">
<title>Lumen Fitness – Business Card</title>
<link href="https://fonts.googleapis.com/css2?family=Source+Sans+3:wght@400;600;700&display=swap" rel="stylesheet">
<style>
  :root {
    --page-bg: #e9e9e6;
    --card-black: #1c1c1c;
    --card-edge: #111111;
    --brand-green: #4cbb47;
    --brand-green-bright: #5fcf4f;
    --text-light: #f2f2f2;
    --divider: #4a4a4a;
  }
  * { box-sizing: border-box; margin: 0; padding: 0; }
  html, body {
    width: 1200px;
    height: 844px;
    overflow: hidden;
  }
  body {
    background: var(--page-bg);
    font-family: "Source Sans 3", "Myriad Pro", Arial, sans-serif;
    position: relative;
  }
  .card {
    position: absolute;
    top: 268px;
    width: 540px;
    height: 308px;
    background: radial-gradient(ellipse at 50% 30%, #262626 0%, var(--card-black) 70%);
    border-radius: 4px;
    box-shadow: 0 2px 0 var(--card-edge), 0 10px 24px rgba(0,0,0,0.25);
    color: var(--text-light);
    overflow: hidden;
  }
  .card--front { left: 40px; }
  .card--back  { left: 620px; }

  /* Front: brand */
  .brand {
    position: absolute;
    top: 62px;
    left: 0;
    right: 0;
    display: flex;
    align-items: center;
    justify-content: center;
    gap: 12px;
  }
  .brand__square {
    width: 22px;
    height: 22px;
    background: var(--brand-green);
  }
  .brand__name {
    font-weight: 700;
    font-size: 40px;
    letter-spacing: 0.5px;
    color: var(--brand-green);
    text-transform: uppercase;
    line-height: 1;
    white-space: nowrap;
  }

  /* Front: details */
  .person {
    position: absolute;
    top: 150px;
    right: 290px;
    text-align: right;
    white-space: nowrap;
  }
  .person__name {
    color: var(--brand-green);
    font-size: 24px;
    font-weight: 400;
    line-height: 1.05;
  }
  .person__title {
    font-size: 15px;
    line-height: 1.2;
  }
  .person__address {
    margin-top: 14px;
    font-size: 16px;
    line-height: 1.15;
  }
  .details-divider {
    position: absolute;
    top: 150px;
    left: 264px;
    width: 1px;
    height: 100px;
    background: var(--divider);
  }
  .contact-list {
    position: absolute;
    top: 150px;
    left: 280px;
    list-style: none;
    white-space: nowrap;
  }
  .contact-list__item {
    display: flex;
    align-items: center;
    gap: 10px;
    height: 25px;
    font-size: 16px;
  }
  .contact-list__icon {
    width: 18px;
    height: 18px;
    border-radius: 2px;
    background: var(--brand-green);
    display: flex;
    align-items: center;
    justify-content: center;
    flex: none;
  }

  /* Back */
  .card--back .brand {
    top: 0;
    bottom: 0;
    flex-direction: column;
    gap: 16px;
  }
  .card--back .brand__square {
    width: 44px;
    height: 44px;
    background: var(--brand-green-bright);
  }
  .card--back .brand__name {
    font-size: 50px;
    color: var(--brand-green-bright);
  }
</style>
</head>
<body>

  <section class="card card--front" aria-label="Business card front">
    <div class="brand">
      <span class="brand__square"></span>
      <span class="brand__name">Lumen Fitness</span>
    </div>

    <div class="person">
      <p class="person__name">Daniel Reyes</p>
      <p class="person__title">Managing Director</p>
      <p class="person__address">48 Harbor Lane, Suite 210<br>Eastvale, OR 97402</p>
    </div>

    <div class="details-divider"></div>

    <ul class="contact-list">
      <li class="contact-list__item">
        <span class="contact-list__icon">
          <svg width="12" height="12" viewBox="0 0 12 12" aria-hidden="true"><path d="M2 4.5a4 2 0 0 1 8 0v1H8V4.5H4v1H2z M3 6.5h6l1 3.5H2z" fill="#fff"/></svg>
        </span>
        (055)-318-2046
      </li>
      <li class="contact-list__item">
        <span class="contact-list__icon">
          <svg width="12" height="12" viewBox="0 0 12 12" aria-hidden="true"><rect x="3.5" y="1" width="5" height="10" rx="1" fill="#fff"/><rect x="4.5" y="2.5" width="3" height="6" fill="#4cbb47"/></svg>
        </span>
        555-210-4837
      </li>
      <li class="contact-list__item">
        <span class="contact-list__icon">
          <svg width="12" height="12" viewBox="0 0 12 12" aria-hidden="true"><rect x="1.5" y="3" width="9" height="6.5" fill="#fff"/><path d="M1.5 3l4.5 3.5L10.5 3" stroke="#4cbb47" stroke-width="1" fill="none"/></svg>
        </span>
        hello@lumenfit.com
      </li>
      <li class="contact-list__item">
        <span class="contact-list__icon">
          <svg width="12" height="12" viewBox="0 0 12 12" aria-hidden="true"><path d="M5 7L7 5M4.2 5.6L3 6.8a1.6 1.6 0 0 0 2.2 2.2l1.2-1.2M7.8 6.4L9 5.2A1.6 1.6 0 0 0 6.8 3L5.6 4.2" stroke="#fff" stroke-width="1.3" fill="none" stroke-linecap="round"/></svg>
        </span>
        www.lumenfit.com
      </li>
    </ul>
  </section>

  <section class="card card--back" aria-label="Business card back">
    <div class="brand">
      <span class="brand__square"></span>
      <span class="brand__name">Lumen Fitness</span>
    </div>
  </section>

</body>
</html>
```